Web Design Project - Investor Services

I would like a simple and elegant web design for my company "Torvelo Management". The company will provide services to Corporate and Institutional investors for their needs with local/foreign investment vehicles. The website will have four pages to start: home, about us, services, contact.
I already chose a logo, and I will attach the source file. The color that I will most probably use for the logo will be blue, and i also like grey with a white background. For the website I would like to see light colors, maybe light green or grey, with the logo either in blue, grey or white (depeding on the background).
Target Market(s)
Investment managers and tax/legal advisors from top firms. This is the reason why I want something simple and elegant.
Industry/Entity Type
Investment
Requirements
Nice to have
- I do not want many pictures in the website, but I might include a couple of pictures of Madrid and maybe a picture of myself in the about us page (still deciding). I will attach some pictures of Madrid that I like, but feel free to search for others - i have others but i am not able to attach all of them.

```html
<!DOCTYPE html>
<html lang="en">
<head>
<meta charset="utf-8">
<title>Torvelo Management</title>
<link rel="stylesheet" href="https://fonts.googleapis.com/css2?family=Fira+Sans+Condensed:wght@300;400;500&display=swap">
<style>
  :root {
    --page-bg: #ffffff;
    --brand-blue: #3a8fcb;
    --nav-top: #62aee6;
    --nav-bottom: #3b8ed2;
    --nav-divider: #9fcdf0;
    --body-text: #4a4a4a;
    --muted-text: #7a7a7a;
    --panel-bg: #ececec;
    --field-border: #c9c9c9;
    --footer-bg: #2b6592;
    --footer-edge: #1f4f76;
    --footer-text: #e8f1f8;
    --footer-active: #0d2a44;
    --icon-bg: #3d7fbf;
  }
  * { box-sizing: border-box; margin: 0; padding: 0; }
  html, body { width: 1200px; height: 918px; overflow: hidden; background: var(--page-bg); }
  body { position: relative; font-family: "Fira Sans Condensed", Arial, sans-serif; font-weight: 300; color: var(--body-text); }

  .hero {
    position: absolute; left: 155px; top: 0; width: 892px; height: 393px;
    border-radius: 0 0 30px 30px; overflow: hidden;
    border: 1px solid #d4d4d4; border-top: none;
    background: linear-gradient(180deg, #5f88a4 0%, #8fa9bb 30%, #c9c3cb 60%, #d9c7cf 78%, #8d9aa6 100%);
  }
  .hero-towers {
    position: absolute; left: 0; bottom: 0; width: 100%; height: 100%;
  }
  .brand {
    position: absolute; left: 242px; top: 18px;
    color: #ffffff; font-size: 34px; font-weight: 300; letter-spacing: 0.5px;
  }

  .main-nav {
    position: absolute; left: 208px; top: 364px; width: 781px; height: 55px;
    background: linear-gradient(180deg, var(--nav-top), var(--nav-bottom));
    border-radius: 2px;
  }
  .main-nav a {
    position: absolute; top: 0; line-height: 55px; transform: translateX(-50%);
    color: #ffffff; text-decoration: none; font-size: 16px; font-weight: 500;
  }
  .nav-divider { position: absolute; top: 20px; width: 1px; height: 16px; background: var(--nav-divider); }

  .welcome { position: absolute; left: 210px; top: 453px; width: 472px; }
  .welcome h1 { color: var(--brand-blue); font-size: 22px; font-weight: 500; margin-bottom: 14px; }
  .welcome p { font-size: 16px; line-height: 23px; text-align: justify; margin-bottom: 23px; }

  .contact-panel {
    position: absolute; left: 712px; top: 457px; width: 271px; height: 309px;
    background: var(--panel-bg); border-radius: 8px;
  }
  .contact-panel h2 { position: absolute; left: 19px; top: 13px; color: var(--brand-blue); font-size: 22px; font-weight: 500; }
  .contact-panel .intro { position: absolute; left: 21px; top: 41px; width: 240px; font-size: 16px; line-height: 20px; color: var(--muted-text); text-align: justify; }
  .field {
    position: absolute; left: 23px; width: 221px; background: #fff;
    border: 1px solid var(--field-border); font: 300 16px "Fira Sans Condensed", Arial, sans-serif;
    color: var(--body-text); padding: 6px 8px;
  }
  .field.name { top: 89px; height: 29px; }
  .field.email { top: 124px; height: 29px; }
  .field.query { top: 159px; height: 103px; resize: none; }
  .submit {
    position: absolute; left: 23px; top: 268px; width: 221px; height: 29px;
    border: 1px solid var(--field-border);
    background: linear-gradient(90deg, #cfcfcf, #ffffff 50%, #d6d6d6);
    font: 400 16px "Fira Sans Condensed", Arial, sans-serif; color: #333;
  }

  .site-footer {
    position: absolute; left: 0; top: 809px; width: 1200px; height: 109px;
    background: var(--footer-bg); border-top: 3px solid var(--footer-edge);
    text-align: center; color: var(--footer-text); font-size: 13px; font-weight: 400;
  }
  .footer-nav { position: absolute; top: 17px; left: 0; width: 100%; }
  .footer-nav a { color: var(--footer-text); text-decoration: none; }
  .footer-nav a.active { color: var(--footer-active); }
  .footer-nav .sep { margin: 0 9px; }
  .copyright { position: absolute; top: 38px; left: 0; width: 100%; }
  .social { position: absolute; top: 64px; width: 23px; height: 23px; background: var(--icon-bg); border: 1px solid #1e5a90; border-radius: 3px; }
</style>
</head>
<body>
  <header class="hero">
    <svg class="hero-towers" viewBox="0 0 892 393" preserveAspectRatio="none" role="img" aria-label="Photograph of Madrid business district skyscrapers against a pale evening sky">
      <rect width="892" height="393" fill="none"/>
    </svg>
    <div class="brand">Torvelo Management</div>
  </header>

  <nav class="main-nav">
    <a href="#" style="left:112px">Home</a>
    <span class="nav-divider" style="left:195px"></span>
    <a href="#" style="left:276px">About Us</a>
    <span class="nav-divider" style="left:370px"></span>
    <a href="#" style="left:448px">Services</a>
    <span class="nav-divider" style="left:538px"></span>
    <a href="#" style="left:625px">Contact Us</a>
  </nav>

  <section class="welcome">
    <h1>Welcome to Torvelo Management</h1>
    <p>The company provide services to Corporate and Institutional investors for their needs with local/foreign investment vehicles.</p>
    <p>The company provide services to Corporate and Institutional investors for their needs with local/foreign investment vehicles. The company provide services to Corporate and Institutional investors for their needs with local/foreign investment vehicles.</p>
    <p>The company provide services to Corporate and Institutional investors for their needs with local/foreign investment vehicles. The company provide services to Corporate and Institutional investors for their needs with local/foreign investment vehicles.</p>
  </section>

  <aside class="contact-panel">
    <h2>Contact Us</h2>
    <p class="intro">Please fill the form to submit your query :</p>
    <input class="field name" type="text" placeholder="Name">
    <input class="field email" type="text" placeholder="Email id">
    <textarea class="field query" placeholder="Query"></textarea>
    <button class="submit" type="button">Submit</button>
  </aside>

  <footer class="site-footer">
    <div class="footer-nav">
      <a href="#" class="active">Home</a><span class="sep">|</span><a href="#">About Us</a><span class="sep">|</span><a href="#">Services</a><span class="sep">|</span><a href="#">Contact Us</a>
    </div>
    <div class="copyright">Copyright@2013, Torvelo Management</div>
    <span class="social" style="left:571px"></span>
    <span class="social" style="left:600px"></span>
  </footer>
</body>
</html>
```